Business card for Luxury Portable Restroom Trailer company

We are a Luxury Portable Restroom Trailer Company Called FALCRIDGE HIRES. Based in Orange County California. We provide portable restroom trailers for events, such as, Weddings, Concerts, Charity events, Sporting events, Tournaments, Corporate events, ect. We rent and Sell the Luxury restrooms. Our colors are white, grey, and Orange. As you will see in the logo we uploaded.
There are 2 people in the company so the names and titles will change for the 3 people but card will remain the same. Here is the information for each Person: Dwight Penner CFO 555 318-0476
next Person: Leon Marchetti VP 555 318-0476
Next Person: Owen Marchetti CEO 555 318-0476
Information to include on the card: Luxury Restroom Trailers Rental and Sales. Weddings, Concerts, Charity, Sporting and Corp. Events.

```html
<!DOCTYPE html>
<html lang="en">
<head>
<meta charset="utf-8">
<title>Falcridge Hires – Business Card</title>
<link href="https://fonts.googleapis.com/css2?family=Montserrat:wght@400;600;700;800&family=Open+Sans:wght@400&display=swap" rel="stylesheet">
<style>
  :root {
    --page-bg: #2a2a2b;
    --card-light: #6a6a6c;
    --card-dark: #4a4a4c;
    --white: #ffffff;
    --soft-white: #e6e6e6;
    --orange: #e8661f;
  }
  * { box-sizing: border-box; margin: 0; padding: 0; }
  html, body { width: 1200px; height: 1200px; overflow: hidden; }
  body {
    background: var(--page-bg);
    display: flex;
    flex-direction: column;
    align-items: center;
    justify-content: center;
    gap: 60px;
    font-family: "Montserrat", sans-serif;
    color: var(--white);
  }
  .card {
    position: relative;
    width: 700px;
    height: 400px;
    background: radial-gradient(ellipse at 50% 40%, var(--card-light), var(--card-dark) 80%);
    box-shadow: 0 10px 30px rgba(0,0,0,.45);
  }

  /* Front */
  .card--front {
    display: flex;
    flex-direction: column;
    align-items: center;
    justify-content: center;
  }
  .brand-frame {
    border: 5px solid var(--white);
    padding: 34px 36px;
    margin-bottom: 26px;
  }
  .brand-name {
    font-weight: 800;
    font-size: 50px;
    letter-spacing: 2px;
    line-height: 1;
    color: var(--white);
    white-space: nowrap;
  }
  .services {
    font-family: "Open Sans", sans-serif;
    font-size: 17px;
    line-height: 1.55;
    text-align: center;
    color: var(--soft-white);
  }

  /* Back */
  .identity {
    position: absolute;
    left: 30px;
    top: 128px;
    width: 255px;
    text-align: right;
  }
  .identity__name {
    font-weight: 700;
    font-size: 30px;
    color: var(--white);
    white-space: nowrap;
  }
  .identity__title {
    font-size: 17px;
    color: var(--soft-white);
    margin-top: 6px;
  }
  .divider {
    position: absolute;
    left: 302px;
    top: 120px;
    width: 2px;
    height: 108px;
    background: var(--orange);
  }
  .contact-list {
    position: absolute;
    left: 322px;
    top: 122px;
    list-style: none;
  }
  .contact-list li {
    display: flex;
    align-items: center;
    gap: 9px;
    font-size: 17px;
    color: var(--soft-white);
    height: 34px;
    white-space: nowrap;
  }
  .contact-list svg { width: 14px; height: 14px; fill: var(--white); flex: none; }
  .address {
    position: absolute;
    left: 70px;
    top: 290px;
    font-size: 17px;
    color: var(--soft-white);
  }
  .mark {
    position: absolute;
    right: 26px;
    top: 150px;
    width: 110px;
    display: flex;
    flex-direction: column;
    align-items: center;
    gap: 8px;
  }
  .mark__circle {
    width: 46px;
    height: 46px;
    border: 4px solid var(--orange);
    border-radius: 50%;
  }
  .mark__name {
    font-weight: 700;
    font-size: 11px;
    color: var(--orange);
    white-space: nowrap;
  }
</style>
</head>
<body>
  <section class="card card--front">
    <div class="brand-frame">
      <div class="brand-name">FALCRIDGE HIRES</div>
    </div>
    <p class="services">
      Luxury Restroom | Trailers Rental and Sales | Weddings |<br>
      Concerts | Charity | Sporting and Corp. Events
    </p>
  </section>

  <section class="card card--back">
    <div class="identity">
      <div class="identity__name">Dwight Penner</div>
      <div class="identity__title">CFO</div>
    </div>
    <div class="divider"></div>
    <ul class="contact-list">
      <li>
        <svg viewBox="0 0 24 24" aria-hidden="true"><path d="M6.6 10.8a15.1 15.1 0 0 0 6.6 6.6l2.2-2.2a1 1 0 0 1 1-.25 11.4 11.4 0 0 0 3.6.57 1 1 0 0 1 1 1V20a1 1 0 0 1-1 1A17 17 0 0 1 3 4a1 1 0 0 1 1-1h3.5a1 1 0 0 1 1 1c0 1.25.2 2.45.57 3.57a1 1 0 0 1-.25 1z"/></svg>
        555 318-0476
      </li>
      <li>
        <svg viewBox="0 0 24 24" aria-hidden="true"><path d="M2 5h20v2l-10 6L2 7zM2 9l10 6 10-6v10H2z"/></svg>
        info@falcridgehires.com
      </li>
      <li>
        <svg viewBox="0 0 24 24" aria-hidden="true"><path d="M12 2a10 10 0 1 0 0 20 10 10 0 0 0 0-20zm7.9 9h-3.4a15 15 0 0 0-1.3-6 8 8 0 0 1 4.7 6zM12 4c.9 1.2 2.2 3.6 2.5 7h-5C9.8 7.6 11.1 5.2 12 4zM8.8 5a15 15 0 0 0-1.3 6H4.1a8 8 0 0 1 4.7-6zM4.1 13h3.4a15 15 0 0 0 1.3 6 8 8 0 0 1-4.7-6zM12 20c-.9-1.2-2.2-3.6-2.5-7h5c-.3 3.4-1.6 5.8-2.5 7zm3.2-1a15 15 0 0 0 1.3-6h3.4a8 8 0 0 1-4.7 6z"/></svg>
        www.falcridgehires.com
      </li>
    </ul>
    <p class="address">4820 Harbor Vale Road Tustin California 92780</p>
    <div class="mark">
      <span class="mark__circle"></span>
      <span class="mark__name">FALCRIDGE HIRES</span>
    </div>
  </section>
</body>
</html>
```